Business Cards - Brightpath Horizon

need to design unique business card for my mortgage business. I need to design credit card style business card for my business or any unique idea that you might have

Target Market(s)

Home Loan customers

Industry/Entity Type

Mortgage Brokerage

Contact Information for Business Card

please design credit card style or very unique style business card

Colors

Designer to choose colors to be used in the design.

Requirements
Must have
• Name
• position
• Phone number
• fax number
• email address
• website address
• social media address
• All above fields will be provided once design in finalised

```html
<!DOCTYPE html>
<html lang="en">
<head>
<meta charset="utf-8">
<title>Brightpath Horizon – Business Cards</title>
<link rel="stylesheet" href="https://fonts.googleapis.com/css2?family=Work+Sans:wght@400;500&display=swap">
<style>
  :root {
    --backdrop: #1c1c1e;
    --card-white: #ffffff;
    --brand-orange: #f58b22;
    --brand-blue: #324c9e;
    --accent-sky: #29a3dc;
    --ink: #3a3a3a;
  }
  * { box-sizing: border-box; margin: 0; padding: 0; }
  html, body { width: 1200px; height: 897px; overflow: hidden; }
  body {
    background: var(--backdrop);
    font-family: "Work Sans", sans-serif;
    position: relative;
  }
  .card {
    position: absolute;
    left: 303px;
    width: 595px;
    height: 338px;
    border-radius: 20px;
    overflow: hidden;
  }
  .card-front { top: 92px; background: var(--card-white); }
  .card-back { top: 469px; background: var(--brand-orange); }

  .footer-stripe {
    position: absolute;
    left: 0; bottom: 26px;
    width: 595px; height: 5px;
    background: var(--brand-orange);
  }
  .footer-band {
    position: absolute;
    left: 0; bottom: 0;
    width: 595px; height: 22px;
    background: var(--brand-blue);
  }

  .brand-name {
    position: absolute;
    font-weight: 500;
    white-space: nowrap;
    letter-spacing: 1px;
  }
  .card-front .brand-name {
    left: 55px; top: 172px;
    width: 240px;
    font-size: 24px;
    color: var(--brand-blue);
    text-align: center;
  }
  .card-front .brand-dot {
    position: absolute;
    left: 159px; top: 128px;
    width: 32px; height: 32px;
    border-radius: 50%;
    background: var(--brand-orange);
  }

  .divider {
    position: absolute;
    left: 307px; top: 89px;
    width: 2px; height: 158px;
    background: var(--brand-blue);
  }

  .contact { position: absolute; left: 339px; top: 82px; color: var(--ink); }
  .person-name {
    font-size: 22px;
    font-weight: 400;
    letter-spacing: 1.6px;
    color: var(--accent-sky);
    line-height: 1;
  }
  .person-role { font-size: 14px; font-weight: 400; margin-top: 10px; letter-spacing: 0.6px; }
  .address { font-size: 13.5px; line-height: 17px; margin-top: 17px; }
  .channels { list-style: none; margin-top: 18px; font-size: 13.5px; line-height: 17.5px; }
  .channels li { display: flex; align-items: center; gap: 8px; }
  .channels svg { width: 9px; height: 9px; flex: none; }

  .card-back .brand-name {
    left: 0; top: 140px;
    width: 595px;
    text-align: center;
    font-size: 34px;
    color: var(--card-white);
  }
  .card-back .brand-dot {
    position: absolute;
    left: 279px; top: 88px;
    width: 38px; height: 38px;
    border-radius: 50%;
    background: var(--card-white);
  }
  .back-website {
    position: absolute;
    left: 0; top: 299px;
    width: 595px;
    text-align: center;
    font-size: 13px;
    letter-spacing: 1.6px;
    color: var(--card-white);
  }
</style>
</head>
<body>

<section class="card card-front">
  <div class="footer-stripe"></div>
  <div class="footer-band"></div>

  <span class="brand-dot"></span>
  <div class="brand-name">Brightpath Horizon</div>

  <div class="divider"></div>

  <div class="contact">
    <h1 class="person-name">DANIEL HARPER</h1>
    <p class="person-role">Founder</p>
    <p class="address">2480 Harbor View Dr.<br>Coral Bay, FL 33100</p>
    <ul class="channels">
      <li>
        <svg viewBox="0 0 10 10"><path d="M2 1 L4 1 L4.6 3 L3.4 3.8 C4 5.2 4.8 6 6.2 6.6 L7 5.4 L9 6 L9 8 C9 8.6 8.6 9 8 9 C4.4 9 1 5.6 1 2 C1 1.4 1.4 1 2 1 Z" fill="var(--accent-sky)"/></svg>
        555-310-4826
      </li>
      <li>
        <svg viewBox="0 0 10 10"><rect x="0.8" y="2" width="8.4" height="6" fill="none" stroke="var(--accent-sky)" stroke-width="1"/><path d="M1 2.3 L5 5.3 L9 2.3" fill="none" stroke="var(--accent-sky)" stroke-width="1"/></svg>
        hello@brightpathmail.com
      </li>
      <li>
        <svg viewBox="0 0 10 10"><circle cx="5" cy="5" r="4" fill="none" stroke="var(--accent-sky)" stroke-width="1"/><ellipse cx="5" cy="5" rx="1.8" ry="4" fill="none" stroke="var(--accent-sky)" stroke-width="0.8"/><path d="M1 5 H9" stroke="var(--accent-sky)" stroke-width="0.8"/></svg>
        www.BrightpathHorizon.com
      </li>
    </ul>
  </div>
</section>

<section class="card card-back">
  <span class="brand-dot"></span>
  <div class="brand-name">Brightpath Horizon</div>
  <p class="back-website">www.yourwebsite.com</p>
</section>

</body>
</html>
```